Modern card design needed for building development company

We are looking for a sharp modern new look for our business cards.
We are a New Zealand based company called TKR Ventures NZ LTD that specialises in subdividing large sections, housing and commercial buildings.
We have attached a photo of the current logo and would like to see it improved somehow as it looks a bit dated.
We are open to any colours.

Target Market(s)

Investors, Property buyers

Industry/Entity Type

Investment

Contact Information for Business Card

TKR VENTURES NZ LTD
www.tkrventuresnz.co.nz

Damon Whitcombe
Phone +64 21 938 104
Email dpwhitcombe@korumail.co.nz

Font styles to use
Serif
Sans Serif

Colors
0792cd
33a6d7
85cae6
6b449b
886aae
f04a50
ec1f27
f37122
f68d4d

Requirements
Must have
• Please try and make the logo more modern or if you have a similar one we would like to see it.

```html
<!DOCTYPE html>
<html lang="en">
<head>
<meta charset="utf-8">
<title>TKR Ventures NZ LTD – Business Card</title>
<link rel="stylesheet" href="https://fonts.googleapis.com/css2?family=Open+Sans:wght@400;700&display=swap">
<style>
  :root {
    --backdrop: #3a3532;
    --card-black: #0d0d0d;
    --card-red: #ae2024;
    --brand-gold: #f2c61f;
    --text-light: #d9d9d9;
    --divider: #555555;
    --icon: #bdbdbd;
  }
  * { margin: 0; padding: 0; box-sizing: border-box; }
  html, body {
    width: 1200px;
    height: 900px;
    overflow: hidden;
    background: var(--backdrop);
    font-family: "Open Sans", Arial, sans-serif;
  }
  .canvas {
    position: relative;
    width: 1200px;
    height: 900px;
  }
  .card {
    position: absolute;
    top: 307px;
    width: 500px;
    height: 286px;
    border-radius: 3px;
    box-shadow: 0 14px 30px rgba(0,0,0,0.45);
  }
  .card--front { left: 70px; background: var(--card-black); }
  .card--back  { left: 630px; background: var(--card-red); }

  .brand {
    position: absolute;
    left: 0;
    right: 0;
    display: flex;
    align-items: center;
    justify-content: center;
    gap: 10px;
  }
  .brand__mark {
    width: 16px;
    height: 16px;
    background: var(--brand-gold);
  }
  .brand__name {
    font-weight: 700;
    font-size: 20px;
    letter-spacing: 1px;
    color: var(--brand-gold);
  }
  .card--front .brand { top: 58px; }
  .card--back .brand { top: 128px; }
  .card--back .brand__name { font-size: 24px; }

  .holder-name {
    position: absolute;
    left: 40px;
    top: 180px;
    font-weight: 700;
    font-size: 17px;
    color: var(--brand-gold);
    letter-spacing: 0.2px;
  }
  .divider {
    position: absolute;
    left: 245px;
    top: 120px;
    width: 1px;
    height: 130px;
    background: var(--divider);
  }
  .contact-list {
    position: absolute;
    left: 262px;
    top: 128px;
    list-style: none;
  }
  .contact-list li {
    display: flex;
    align-items: center;
    gap: 8px;
    height: 22px;
    font-size: 13px;
    color: var(--text-light);
  }
  .contact-list svg {
    width: 10px;
    height: 10px;
    flex: none;
    fill: none;
    stroke: var(--icon);
    stroke-width: 1.4;
  }
</style>
</head>
<body>
<main class="canvas">
  <section class="card card--front" aria-label="Business card front">
    <div class="brand">
      <span class="brand__mark"></span>
      <span class="brand__name">TKR Ventures NZ LTD</span>
    </div>
    <p class="holder-name">DAMON WHITCOMBE</p>
    <span class="divider"></span>
    <ul class="contact-list">
      <li>
        <svg viewBox="0 0 10 10" aria-hidden="true"><rect x="2.5" y="0.7" width="5" height="8.6" rx="1"/><line x1="4.3" y1="7.8" x2="5.7" y2="7.8"/></svg>
        +64 21 938 104
      </li>
      <li>
        <svg viewBox="0 0 10 10" aria-hidden="true"><rect x="0.7" y="2" width="8.6" height="6" /><polyline points="0.7,2 5,5.5 9.3,2"/></svg>
        dpwhitcombe@korumail.co.nz
      </li>
      <li>
        <svg viewBox="0 0 10 10" aria-hidden="true"><circle cx="5" cy="5" r="4.3"/><ellipse cx="5" cy="5" rx="1.8" ry="4.3"/><line x1="0.7" y1="5" x2="9.3" y2="5"/></svg>
        www.tkrventuresnz.co.nz
      </li>
    </ul>
  </section>

  <section class="card card--back" aria-label="Business card back">
    <div class="brand">
      <span class="brand__mark"></span>
      <span class="brand__name">TKR Ventures NZ LTD</span>
    </div>
  </section>
</main>
</body>
</html>
```